Web app for social movements needs a new look

We are building a Velmora Quill extension called "Pelbo" that helps social movement leaders and advocacy organizations connect with an audience that cares about their cause, and we need to create a more polished website to explain the extension to prospective users. The extension analyzes articles users are reading online and recommends ways they can take action in their local area on the social and political issues they are reading about. For example, if a user is reading about the climate crisis, the extension might display a banner recommending a rally being held by the Kestrel Movement or an opportunity to canvass or phone bank for a pro-Tallow Harbor Pact political candidate. Organizers with progressive organizations can register for an account on our web portal to start posting actions or events that will then be recommended to users through the browser extension if they are reading a relevant article.

We are planning for an upcoming "soft launch" and would like to create a more polished version of our website. The design should include:
– A user-facing page that that concisely explains how the Quill extension works and links to the Quill web store where users can download Pelbo.
– An organizer-facing page that outlines the steps involved for organizers to recommend their organization or a specific action to users through Pelbo: register for an account, post an action or event, your action or event is recommended to users.
– An HTML/CSS template for the organizer portal that we can then take and populate with Django forms or other Django content. This template should include a top menu bar. We've provided an example of the extremely barebones template used in our prototype as an example (base.html).
– A redesigned or improved logo, including one version designed to be put on a white background and one version designed to go on a background of a darker color (e.g., orange). Our current logo is provided. Feel free to use this as a starting point or design something completely different.

The design should convey themes of solidarity, bringing people together to effect positive change, and hope for a better future. We expect that organizations and users on the platform will be focused on a range of progressive issues, including racial justice, immigration justice, gender equity, LGBTQ+ rights, workers' rights, and addressing the climate crisis and economic inequality.

Currently, the color scheme of our prototype browser extension is centered around the color orange, but we are open to designers' ideas about other possible color schemes.

```html
<!DOCTYPE html>
<html lang="en">
<head>
<meta charset="utf-8">
<title>Pelbo — Social Movement Leaders</title>
<link href="https://fonts.googleapis.com/css2?family=Roboto:wght@400;500;700;900&display=swap" rel="stylesheet">
<style>
  :root {
    --navy: #153b6d;
    --red: #d5323b;
    --dark: #2b2b2e;
    --white: #ffffff;
    --text-grey: #7a7a7a;
    --hero-a: #6f6a63;
    --hero-b: #a89a86;
  }
  * { box-sizing: border-box; margin: 0; padding: 0; }
  html, body { width: 1200px; height: 2416px; overflow: hidden; }
  body { position: relative; font-family: "Roboto", Arial, sans-serif; background: var(--white); color: var(--dark); }
  ul { list-style: none; }
  a { text-decoration: none; }
  .abs { position: absolute; }
  .btn {
    position: absolute; background: var(--red); color: var(--white);
    font-weight: 700; font-size: 14px; letter-spacing: 0.5px; text-transform: uppercase;
    border-radius: 24px; display: flex; align-items: center; justify-content: center; z-index: 2;
  }

  /* Brand lockup */
  .brand { position: absolute; display: flex; align-items: center; gap: 16px; color: var(--white);
    font-weight: 700; font-size: 40px; line-height: 1; z-index: 3; }
  .brand-dot { display: block; width: 78px; height: 78px; border: 3px solid var(--white); border-radius: 50%; flex: none; }
  .brand-header { left: 140px; top: 30px; }
  .brand-footer { left: 140px; top: 2160px; }

  /* Hero */
  .hero { left: 0; top: 0; width: 1200px; height: 600px;
    background: linear-gradient(120deg, var(--hero-a), var(--hero-b) 55%, #5d6068); }
  .hero::after { content: ""; position: absolute; inset: 0; background: rgba(0,0,0,0.25); }
  .menu-icon { left: 1012px; top: 56px; width: 40px; z-index: 2; }
  .menu-icon span { display: block; height: 5px; background: var(--white); margin-bottom: 9px; border-radius: 2px; }
  .hero-title { left: 0; top: 280px; width: 1200px; text-align: center; color: var(--white);
    font-size: 62px; font-weight: 700; z-index: 2; }
  .hero-btn { left: 520px; top: 390px; width: 160px; height: 56px; }
  .dots { left: 1068px; top: 542px; display: flex; gap: 12px; z-index: 2; }
  .dots span { width: 13px; height: 13px; border-radius: 50%; background: var(--white); }
  .dots span + span { background: var(--red); }

  /* How it works band */
  .how { left: 0; top: 590px; width: 1200px; height: 390px; z-index: 1; }
  .how-title { left: 140px; top: 630px; width: 420px; color: var(--white); font-size: 40px; font-weight: 700; line-height: 1.15; z-index: 2; }
  .how-text { left: 578px; top: 622px; width: 480px; color: var(--white); font-size: 13px; line-height: 1.55; z-index: 2; }
  .how-btn { left: 580px; top: 796px; width: 134px; height: 46px; }

  /* Overview */
  .overview-bg { left: 0; top: 860px; width: 1200px; height: 510px;
    background: linear-gradient(180deg, #f2f1ef, #e4e0db 50%, #f0efed); }
  .section-title { left: 0; width: 1200px; text-align: center; color: var(--navy); font-weight: 700; }
  .overview-title { top: 1010px; font-size: 56px; }
  .section-text { left: 170px; width: 860px; text-align: center; color: var(--text-grey); font-size: 15px; line-height: 1.75; }
  .overview-text { top: 1088px; }
  .overview-btn { left: 532px; top: 1262px; width: 136px; height: 50px; }

  /* Photo row */
  .photo { top: 1370px; height: 344px; }
  .photo-1 { left: 0; width: 362px; background: linear-gradient(135deg, #9c8f80, #5a5654); }
  .photo-2 { left: 370px; width: 460px; background: linear-gradient(135deg, #b5aa98, #6f6b66); }
  .photo-3 { left: 838px; width: 362px; background: linear-gradient(135deg, #8b7d6c, #4e4d50); }

  /* Questions */
  .questions-bg { left: 0; top: 1714px; width: 1200px; height: 440px;
    background: linear-gradient(180deg, #f4f3f1, #e6e2dd 60%, #efedea); }
  .questions-title { top: 1790px; font-size: 56px; }
  .questions-text { top: 1870px; }
  .questions-btn { left: 526px; top: 1966px; width: 148px; height: 50px; }

  /* Footer */
  .footer { left: 0; top: 2090px; width: 1200px; height: 326px; }
  .foot-col { top: 2163px; color: var(--white); }
  .foot-col h3 { font-size: 19px; font-weight: 700; margin-bottom: 12px; text-transform: uppercase; }
  .foot-col li { font-size: 13px; line-height: 1.6; }
  .col-menu { left: 504px; }
  .col-links { left: 645px; }
  .col-news { left: 840px; width: 240px; }
  .col-news p { font-size: 12px; margin-bottom: 18px; }
  .signup { display: flex; }
  .signup .field { width: 116px; height: 44px; background: var(--white); border-radius: 22px 0 0 22px;
    color: var(--dark); font-size: 12px; display: flex; align-items: center; padding-left: 18px; }
  .signup .go { width: 92px; height: 44px; background: var(--red); border-radius: 0 22px 22px 0;
    font-size: 13px; font-weight: 700; display: flex; align-items: center; justify-content: center; }
  .social { left: 934px; top: 2348px; display: flex; gap: 10px; }
  .social span { width: 32px; height: 32px; border-radius: 50%; background: var(--white); }
  .legal { left: 140px; top: 2372px; color: var(--white); font-size: 12px; }
</style>
</head>
<body>

  <!-- Hero -->
  <div class="abs hero" role="img" aria-label="Photo of a young activist shouting into a megaphone at a protest crowd"></div>
  <div class="brand brand-header"><span class="brand-dot"></span><span>Pelbo</span></div>
  <div class="abs menu-icon" aria-label="Menu"><span></span><span></span><span></span></div>
  <h1 class="abs hero-title">SOCIAL MOVEMENT LEADERS</h1>
  <a class="btn hero-btn">Get Started</a>
  <div class="abs dots"><span></span><span></span></div>

  <!-- Overview background (under the band) -->
  <div class="abs overview-bg" role="img" aria-label="Faded photo of a protester raising a fist in a crowd"></div>

  <!-- How it works -->
  <svg class="abs how" viewBox="0 0 1200 390" aria-hidden="true">
    <polygon points="0,0 1200,0 1200,270 600,380 0,270" fill="#153b6d"/>
  </svg>
  <h2 class="abs how-title">HOW THE QUILL EXTENSION WORKS</h2>
  <p class="abs how-text">Lorem ipsum dolor sit amet, consectetur adipiscing elit, sed do eiusmod tempor incididunt ut labore et dolore magna aliqua. Quis ipsum suspendisse ultrices gravida. Risus commodo viverra maecenas accumsan lacus vel facilisis. Lorem ipsum dolor sit amet, consectetur adipiscing elit, sed do eiusmod tempor incididunt ut labore et dolore magna aliqua. Quis ipsum suspendisse ultrices gravida. Risus commodo viverra maecenas accumsan lacus vel facilisis.</p>
  <a class="btn how-btn">Read More</a>

  <!-- Overview -->
  <h2 class="abs section-title overview-title">OVERVIEW</h2>
  <p class="abs section-text overview-text">Facilitating social responsibility by connecting the needed individuals and to ways they may impact the real world. Many of us read about social and political issues we care about every day but may not know how to take concrete action to combat injustice and create meaningful change. Pelbo is a Quill extension that analyzes articles you are reading and recommends relevant actions you can take. By connecting you to organizers and movements, Pelbo can help you find ways to take part in building a more just, equitable, and sustainable future.</p>
  <a class="btn overview-btn">Read More</a>

  <!-- Photo row -->
  <div class="abs photo photo-1" role="img" aria-label="Photo of a woman with a megaphone at a rally"></div>
  <div class="abs photo photo-2" role="img" aria-label="Photo of a group of young people holding blank protest signs"></div>
  <div class="abs photo photo-3" role="img" aria-label="Photo of a smiling activist with a megaphone in a crowd"></div>

  <!-- Questions -->
  <div class="abs questions-bg" role="img" aria-label="Faded photo of a protest march"></div>
  <h2 class="abs section-title questions-title">HAVE SOME QUESTIONS?</h2>
  <p class="abs section-text questions-text">Lorem ipsum dolor sit amet, consectetur adipiscing elit, sed do eiusmod tempor incididunt ut labore et dolore magna aliqua. Quis ipsum suspendisse ultrices gravida. Risus commodo viverra maecenas accumsan lacus vel facilisis.</p>
  <a class="btn questions-btn">Contact Us</a>

  <!-- Footer -->
  <svg class="abs footer" viewBox="0 0 1200 326" aria-hidden="true">
    <polygon points="0,40 600,0 1200,40 1200,326 0,326" fill="#2b2b2e"/>
  </svg>
  <div class="brand brand-footer"><span class="brand-dot"></span><span>Pelbo</span></div>
  <div class="abs foot-col col-menu">
    <h3>Menu</h3>
    <ul><li>Home</li><li>About</li><li>Services</li><li>Contact</li></ul>
  </div>
  <div class="abs foot-col col-links">
    <h3>Links</h3>
    <ul><li>Privacy Policy</li><li>Terms and Conditions</li><li>Sitemap</li><li>Information</li></ul>
  </div>
  <div class="abs foot-col col-news">
    <h3>Sign Up Newsletter</h3>
    <p>Get all updates sent straight to your inbox</p>
    <div class="signup"><span class="field">Enter Email</span><span class="go">SIGN UP</span></div>
  </div>
  <div class="abs social" aria-label="Social links"><span></span><span></span><span></span></div>
  <p class="abs legal">© 2022 Pelbo. All rights reserved Privacy &nbsp;|&nbsp; Terms of Use</p>

</body>
</html>
```